Film poster for The Lanterns Stay Lit - a documentary

We need a poster for our documentary, The Lanterns Stay Lit, about how Ancient heroine Antigone finds new life in Beirut’s refugee camps, helping four Syrian women discover the strength to live with joy through the greatest of tragedies. The film is about 20% animated with the rest being vérité footage shot in Beirut, Lebanon. The title will be in Arabic and English.

Please check out our trailer here: https://www.fundmarrow.example/projects/417306582/the-lanterns-stay-lit?ref=qopxt3

We've included some assets from the film as well as style references of other film posters we've liked.

The designer we use will also get a credit in the film.

Target Market(s)

Documentary film festivals

Industry/Entity Type

Film Production

Font styles to use
Sans Serif

Colors

Designer to choose colors to be used in the design.

Requirements
Must have
• The Title in Both English and Arabic (Can provide the text for the arabic)
• Space at the bottom to overlay film credits
Nice to have
• Include the texture of the wall and perhaps integrate both photographic and graphic imagery
Should not have
• Shouldn't be too busy - minimalistic

```html
<!DOCTYPE html>
<html lang="en">
<head>
<meta charset="utf-8">
<title>The Lanterns Stay Lit — Poster</title>
<link rel="stylesheet" href="https://fonts.googleapis.com/css2?family=Cairo:wght@700&family=Oswald:wght@500;600&display=swap">
<style>
  :root {
    --paper: #ffffff;
    --wall-red: #c9321a;
    --wall-red-deep: #b02a14;
    --wall-red-light: #d43d22;
    --veil-blue: #2b68a0;
    --veil-blue-deep: #245c90;
    --ink-white: #ffffff;
  }
  html, body {
    margin: 0;
    padding: 0;
    width: 810px;
    height: 1200px;
    overflow: hidden;
    background: var(--paper);
  }
  .poster {
    position: relative;
    width: 810px;
    height: 1200px;
    background: var(--paper);
    overflow: hidden;
  }
  .poster__art {
    position: absolute;
    left: 0;
    top: 0;
    width: 810px;
    height: 1200px;
  }
  .title {
    position: absolute;
    left: 0;
    top: 262px;
    width: 810px;
    margin: 0;
    font-family: "Oswald", sans-serif;
    font-weight: 600;
    color: var(--ink-white);
    text-align: center;
    text-transform: uppercase;
    line-height: 1;
    letter-spacing: 2px;
  }
  .title__line {
    display: block;
    position: relative;
    left: 14px;
  }
  .title__line--the { font-size: 118px; height: 124px; }
  .title__line--lanterns { font-size: 138px; height: 146px; }
  .title__line--stay { font-size: 150px; height: 156px; }
  .title__line--lit { font-size: 168px; height: 172px; }
  .title-arabic {
    position: absolute;
    left: 14px;
    top: 862px;
    width: 810px;
    margin: 0;
    font-family: "Cairo", sans-serif;
    font-weight: 700;
    font-size: 60px;
    line-height: 1.3;
    color: var(--ink-white);
    text-align: center;
  }
  .credits {
    position: absolute;
    left: 0;
    top: 1040px;
    width: 810px;
    font-family: "Oswald", sans-serif;
    font-weight: 500;
    color: var(--ink-white);
    text-align: center;
    text-transform: uppercase;
    letter-spacing: 0.2px;
  }
  .credits__row {
    display: flex;
    justify-content: center;
    align-items: center;
    gap: 4px;
    font-size: 12.5px;
    line-height: 1;
    height: 19px;
    white-space: nowrap;
    transform: scaleX(0.78);
  }
  .credits__label {
    font-size: 5px;
    line-height: 1.05;
    width: 22px;
    text-align: right;
    white-space: normal;
  }
</style>
</head>
<body>
  <main class="poster">
    <svg class="poster__art" viewBox="0 0 810 1200" xmlns="http://www.w3.org/2000/svg">
      <defs>
        <radialGradient id="wallGradient" cx="0.5" cy="0.45" r="0.75">
          <stop offset="0" stop-color="var(--wall-red-light)"/>
          <stop offset="0.7" stop-color="var(--wall-red)"/>
          <stop offset="1" stop-color="var(--wall-red-deep)"/>
        </radialGradient>
        <linearGradient id="veilGradient" x1="0" y1="0" x2="1" y2="1">
          <stop offset="0" stop-color="var(--veil-blue)"/>
          <stop offset="1" stop-color="var(--veil-blue-deep)"/>
        </linearGradient>
      </defs>
      <rect class="wall-texture" x="16" y="16" width="780" height="1168" fill="url(#wallGradient)"
            role="img" aria-label="Photographic texture of a cracked red-painted wall"/>
      <path class="veiled-figure" d="M160 1184 L200 320 C210 150 280 46 370 46 C470 46 540 150 590 330 L690 1184 Z"
            fill="url(#veilGradient)"
            role="img" aria-label="Illustration of a woman in a blue veil seen in profile, with trailing leafy vines and white flower sprigs"/>
    </svg>

    <h1 class="title" aria-label="The Lanterns Stay Lit">
      <span class="title__line title__line--the">The</span>
      <span class="title__line title__line--lanterns">Lanterns</span>
      <span class="title__line title__line--stay">Stay</span>
      <span class="title__line title__line--lit">Lit</span>
    </h1>
    <p class="title-arabic" lang="ar" dir="rtl">الفوانيس تبقى مضاءة</p>

    <section class="credits" aria-label="Film credits">
      <div class="credits__row">Studio Name Pictures <span class="credits__label">presents a</span> Producers <span class="credits__label">a film by</span> Script Writer Actor One Actor Two "Movie Title"</div>
      <div class="credits__row"><span class="credits__label">music by</span> The Musician <span class="credits__label">costume design</span> Designer Name <span class="credits__label">edited by</span> Editors Name <span class="credits__label">production design</span> Designers Name <span class="credits__label">photo direction</span> Cinematographer</div>
      <div class="credits__row"><span class="credits__label">exec producer</span> Ex Producer 1 Ex Producer 2 <span class="credits__label">produced by</span> Producer One Producer 2 <span class="credits__label">story by</span> Story Writer</div>
      <div class="credits__row"><span class="credits__label">screenplay by</span> Screen Writer <span class="credits__label">directed by</span> Director Name</div>
    </section>
  </main>
</body>
</html>
```